Tidy paddock Services

After a high quality design website. we are a company that provides services to people that own land and need a hand getting on top of the delayed jobs.
would want a number of tab/ pages for the web page.
Home page / About us page / services page / Gallery page. / Contact us page
we offer a wide range of services .listed below

Stock Work (title)

Stock movement
Break feeding
Temporary staffing

Spraying (title)

Spraying weeds
Spraying gorse

Pastures (title)

Fertilizing
Topping

Building (title)

Habitable sheds
Farm sheds
Sheep yards
Cattle yards
Repair farm buildings
Decks
Retaining walls

Fencing (title)

Stock fencing
Post & rail
Stock yards repair
Electric fencing install & repairs

Water Management (title)

Water trough installation
Water scheme install
Water trough cleaning
Farm water maintenance
Water ponds
Ornamental ponds
Drainage

General (title)

Lawn mowing
Hedge trimming
Pruning trees
Metaling drive ways & races
Water blasting
Small digger work
Little tip truck cartage
Home kill management
Mulching gorse
Section clearing

```html
<!DOCTYPE html>
<html lang="en">
<head>
<meta charset="utf-8">
<title>Tidy paddock Services</title>
<link href="https://fonts.googleapis.com/css2?family=Montserrat:wght@400;500;600;700;800&display=swap" rel="stylesheet">
<style>
:root{
  --green:#5f9e16;
  --green-dark:#4e8a0e;
  --ink:#111;
  --muted:#666;
  --light:#f4fde4;
  --header:#f7fdea;
  --white:#fff;
  --black:#000;
}
*{box-sizing:border-box;margin:0;padding:0}
html,body{width:1200px;height:3861px;overflow:hidden}
body{font-family:"Montserrat",sans-serif;color:var(--ink);background:var(--white);position:relative}
.abs{position:absolute}
.btn{position:absolute;display:flex;align-items:center;justify-content:center;background:var(--green);color:var(--white);font-weight:700;border-radius:30px;font-size:15px}
/* header */
.site-header{position:absolute;left:0;top:0;width:1200px;height:87px;background:var(--header);z-index:3}
.brand{position:absolute;display:flex;align-items:center;gap:10px;font-weight:700;color:var(--green);font-size:22px}
.brand-dot{width:16px;height:16px;border-radius:50%;background:var(--green)}
.nav a{position:absolute;top:38px;font-size:13px;font-weight:500;color:var(--ink);text-decoration:none}
/* hero */
.hero-title{position:absolute;left:110px;font-weight:800}
.hero-sub{position:absolute;left:110px;top:372px;font-size:20px;line-height:33px;font-weight:500;color:#222}
/* section titles */
.h2{position:absolute;font-size:40px;font-weight:700}
.h2 .g{color:var(--green)}
.about-text{position:absolute;left:601px;top:818px;width:390px;font-size:13.5px;line-height:25.6px;color:#555}
/* services */
.services{position:absolute;left:0;top:1253px;width:1200px;height:670px;background:var(--light)}
.card{position:absolute;width:245px;height:251px;background:var(--white);border:1px solid #bbb}
.card.active{background:var(--green);border-color:var(--green);box-shadow:0 4px 14px rgba(0,0,0,.2);z-index:2}
.card .ico{position:absolute;left:20px;top:24px;width:44px;height:44px}
.card h3{position:absolute;left:20px;top:96px;font-size:19px;font-weight:600}
.card ul{position:absolute;left:21px;top:132px;list-style:none;font-size:14.5px;color:var(--muted);line-height:30px}
.card.active h3,.card.active ul{color:var(--white)}
.card .plus{position:absolute;right:-1px;bottom:-1px;width:32px;height:32px;background:var(--green);color:var(--white);font-size:30px;font-weight:700;line-height:30px;text-align:center}
.card.active .plus{background:var(--white);color:var(--green);right:4px;bottom:4px}
/* quote */
.quote-bg{position:absolute;left:0;top:1880px;width:1200px;height:658px;background:linear-gradient(90deg,#7b8a5a 0%,#5e6c3c 30%,#3c3c30 60%,#1d1d1d 100%)}
.field{position:absolute;background:var(--white);border-radius:6px;font-size:14px;color:#666;padding:14px 12px}
/* gallery */
.shot{position:absolute;width:311px;height:269px;border-radius:5px}
/* footer */
.footer{position:absolute;left:0;top:3330px;width:1200px;height:531px;background:var(--black);color:var(--white)}
.fh{position:absolute;font-size:20px;font-weight:600}
.fl{position:absolute;font-size:14px;font-weight:500}
.fb{font-weight:700}
</style>
</head>
<body>

<header class="site-header">
  <div class="brand" style="left:78px;top:30px"><span class="brand-dot"></span>Tidy paddock Services</div>
  <nav class="nav">
    <a style="left:400px">HOME</a>
    <a style="left:480px">ABOUT US</a>
    <a style="left:587px">SERVICES</a>
    <a style="left:690px">GALLERY</a>
    <a style="left:789px">CONTACT US</a>
  </nav>
  <div class="btn" style="left:906px;top:24px;width:181px;height:46px">Request A Quote</div>
</header>

<!-- hero -->
<section class="hero">
  <div class="abs" style="left:0;top:87px;width:1200px;height:603px;background:#f3f5ef"></div>
  <svg class="abs" style="left:0;top:0" width="1200" height="700" viewBox="0 0 1200 700" role="img" aria-label="Worker in orange safety gear trimming a green hedge">
    <defs>
      <linearGradient id="heroPhoto" x1="0" y1="0" x2="1" y2="0">
        <stop offset="0" stop-color="#c9d6a8"/><stop offset=".35" stop-color="#6f8f2c"/><stop offset=".6" stop-color="#e07a1e"/><stop offset="1" stop-color="#4d6e1c"/>
      </linearGradient>
    </defs>
    <path d="M560 87 C500 260 500 480 600 620 L1200 690 L1200 87 Z" fill="url(#heroPhoto)"/>
    <path d="M0 700 L0 690 C300 580 800 590 1200 690 L1200 700 Z" fill="#fff"/>
    <path d="M13 685 C300 585 800 585 1200 688" fill="none" stroke="var(--green)" stroke-width="8"/>
    <circle cx="13" cy="685" r="10" fill="var(--green)"/>
  </svg>
  <div class="hero-title" style="top:205px;font-size:27px;font-weight:700">WELCOME TO</div>
  <div class="hero-title" style="top:242px;font-size:52px;color:var(--green)">TIDY PADDOCK</div>
  <div class="hero-title" style="top:302px;font-size:52px">SERVICES</div>
  <p class="hero-sub">Stock Work, Spraying, Pastures, Building,<br>Fencing, Water Management, General</p>
  <div class="btn" style="left:110px;top:455px;width:148px;height:44px">Get Started</div>
</section>

<!-- about -->
<section class="about">
  <svg class="abs" style="left:120px;top:705px" width="460" height="460" viewBox="0 0 460 460">
    <path d="M30 250 A210 210 0 0 0 370 400" fill="none" stroke="#000" stroke-width="10"/>
    <circle cx="228" cy="228" r="212" fill="#5a5f56" role="img" aria-label="Worker in hard hat and hi-vis jacket repairing a wire fence"/>
    <circle cx="45" cy="103" r="23" fill="var(--green)"/>
  </svg>
  <h2 class="h2" style="left:601px;top:745px"><span class="g">About</span> Us</h2>
  <p class="about-text">Lorem Ipsum is simply dummy text of the printing and typesetting industry. Lorem Ipsum has been the industry's standard dummy text ever since the 1500s, when an unknown printer took a galley of type and scrambled it to make a type specimen book. It has survived not only five centuries, but also the leap into electronic typesetting, remaining essentially unchanged.</p>
  <div class="btn" style="left:601px;top:1056px;width:148px;height:45px">Read More</div>
</section>

<!-- services -->
<section class="services">
  <h2 class="h2" style="left:110px;top:147px;line-height:48px"><span class="g">Our</span><br>Services</h2>

  <div class="card" style="left:353px;top:99px">
    <svg class="ico" viewBox="0 0 44 44"><path d="M6 20 L38 20 L32 42 L12 42 Z" fill="var(--green)"/><circle cx="22" cy="10" r="8" fill="var(--green)"/></svg>
    <h3>Stock Work</h3><ul><li>Stock movement</li><li>Break feeding</li><li>Temporary staffing</li></ul><div class="plus">+</div>
  </div>
  <div class="card active" style="left:595px;top:96px;width:249px;height:257px">
    <svg class="ico" viewBox="0 0 44 44"><rect x="4" y="6" width="14" height="12" fill="#fff"/><circle cx="26" cy="28" r="9" fill="#fff"/></svg>
    <h3>Spraying</h3><ul><li>Spraying weeds</li><li>Spraying gorse</li></ul><div class="plus">+</div>
  </div>
  <div class="card" style="left:843px;top:99px">
    <svg class="ico" viewBox="0 0 44 44"><path d="M8 42 L14 14 L30 14 L38 42 Z" fill="var(--green)"/><circle cx="22" cy="8" r="6" fill="var(--green)"/></svg>
    <h3>Pastures</h3><ul><li>Fertilizing</li><li>Topping</li></ul><div class="plus">+</div>
  </div>

  <div class="card" style="left:109px;top:349px">
    <svg class="ico" viewBox="0 0 44 44"><path d="M2 18 L22 4 L42 18 L38 18 L38 42 L6 42 L6 18 Z" fill="var(--green)"/><rect x="14" y="24" width="16" height="18" fill="#fff"/></svg>
    <h3>Building</h3><ul><li>Habitable sheds</li><li>Farm sheds</li><li>Sheep yards</li></ul><div class="plus">+</div>
  </div>
  <div class="card" style="left:353px;top:349px">
    <svg class="ico" viewBox="0 0 44 44"><g fill="var(--green)"><rect x="2" y="8" width="5" height="34"/><rect x="11" y="8" width="5" height="34"/><rect x="20" y="8" width="5" height="34"/><rect x="29" y="8" width="5" height="34"/><rect x="38" y="8" width="5" height="34"/><rect x="0" y="16" width="44" height="4"/><rect x="0" y="30" width="44" height="4"/></g></svg>
    <h3>Fencing</h3><ul><li>Stock fencing</li><li>Post &amp; rail</li><li>Stock yards repair</li></ul><div class="plus">+</div>
  </div>
  <div class="card" style="left:597px;top:349px">
    <svg class="ico" viewBox="0 0 44 44"><circle cx="22" cy="22" r="19" fill="var(--green)"/><circle cx="22" cy="22" r="9" fill="#fff"/></svg>
    <h3>Water Management</h3><ul><li>Water trough installation</li><li>Water scheme install</li><li>Water trough cleaning</li></ul><div class="plus">+</div>
  </div>
  <div class="card" style="left:842px;top:349px">
    <svg class="ico" viewBox="0 0 44 44"><rect x="30" y="6" width="4" height="36" fill="var(--green)"/><circle cx="32" cy="10" r="8" fill="var(--green)"/><rect x="4" y="38" width="36" height="4" fill="var(--green)"/></svg>
    <h3>General</h3><ul><li>Lawn mowing</li><li>Hedge trimming</li><li>Pruning trees</li></ul><div class="plus">+</div>
  </div>
</section>

<!-- quote -->
<section class="quote">
  <div class="quote-bg" role="img" aria-label="Tractor spraying a green crop field at sunset"></div>
  <svg class="abs" style="left:0;top:1860px" width="1200" height="140" viewBox="0 0 1200 140">
    <path d="M0 0 L1200 0 L1200 52 C900 110 400 145 12 47 L0 44 Z" fill="var(--light)"/>
    <path d="M12 47 C400 145 900 110 1200 52" fill="none" stroke="#000" stroke-width="8"/>
    <circle cx="12" cy="47" r="10" fill="#000"/>
  </svg>
  <h2 class="h2" style="left:601px;top:2040px;color:#fff"><span class="g">Request</span> A Quote</h2>
  <div class="field" style="left:603px;top:2115px;width:231px;height:51px">Name*</div>
  <div class="field" style="left:843px;top:2115px;width:231px;height:51px">Email*</div>
  <div class="field" style="left:603px;top:2177px;width:231px;height:51px">Contact Number*</div>
  <div class="field" style="left:843px;top:2177px;width:231px;height:51px">Service</div>
  <div class="field" style="left:603px;top:2238px;width:471px;height:118px">Your Message*</div>
  <div class="btn" style="left:603px;top:2376px;width:149px;height:45px;background:#fff;color:var(--green)">Submit</div>
</section>

<!-- gallery -->
<section class="gallery">
  <h2 class="h2" style="left:0;width:1200px;text-align:center;top:2612px"><span class="g">Our</span> Gallery</h2>
  <div class="shot" style="left:110px;top:2704px;background:linear-gradient(135deg,#3d5a1a,#a7c27a)" role="img" aria-label="Weed sprayer misting a dandelion"></div>
  <div class="shot" style="left:443px;top:2704px;background:linear-gradient(135deg,#4a3a2a,#5b8fbf)" role="img" aria-label="Gloved hand fertilizing a seedling"></div>
  <div class="shot" style="left:775px;top:2704px;background:linear-gradient(180deg,#9ec0e8,#4d6b8f 60%,#8a8a88)" role="img" aria-label="Blue farm shed with gravel yard"></div>
  <div class="shot" style="left:110px;top:2993px;background:linear-gradient(135deg,#5a3e28,#c9b9a0)" role="img" aria-label="Sheep standing in a wooden barn"></div>
  <div class="shot" style="left:443px;top:2993px;background:linear-gradient(135deg,#3b3f45,#d87a2a)" role="img" aria-label="Workers in hard hats fixing wire fencing"></div>
  <div class="shot" style="left:775px;top:2993px;background:linear-gradient(180deg,#d9dde0,#8e9aa3)" role="img" aria-label="Electric fence warning sign on mesh fence"></div>
</section>

<!-- footer -->
<footer>
  <svg class="abs" style="left:0;top:3320px" width="1200" height="120" viewBox="0 0 1200 120">
    <path d="M0 10 C400 110 800 115 1200 22 L1200 120 L0 120 Z" fill="#000"/>
    <path d="M0 10 C400 100 800 100 1188 22" fill="none" stroke="var(--green)" stroke-width="8"/>
    <circle cx="1188" cy="22" r="10" fill="var(--green)"/>
  </svg>
  <div class="footer" style="top:3430px;height:431px">
    <div class="brand" style="left:100px;top:100px;font-size:19px"><span class="brand-dot"></span>Tidy paddock Services</div>
    <div class="fh" style="left:399px;top:57px">Main Links</div>
    <div class="fl" style="left:401px;top:111px">Home</div>
    <div class="fl" style="left:401px;top:141px">Services</div>
    <div class="fl" style="left:401px;top:171px">About Us</div>
    <div class="fl" style="left:401px;top:201px">Gallery</div>
    <div class="fl" style="left:401px;top:231px">Contact</div>

    <div class="fh" style="left:632px;top:57px">Other Links</div>
    <div class="fl" style="left:634px;top:111px">Privacy Policy</div>
    <div class="fl" style="left:634px;top:141px">Terms and Condition</div>
    <div class="fl" style="left:634px;top:171px">Legal information</div>

    <div class="fh" style="left:884px;top:57px">Contact Details</div>
    <svg class="abs" style="left:884px;top:112px" width="14" height="14" viewBox="0 0 14 14"><path d="M3 1 L6 4 L4 6 C5 8 6 9 8 10 L10 8 L13 11 L11 13 C6 13 1 8 1 3 Z" fill="#fff"/></svg>
    <div class="fl fb" style="left:903px;top:110px">Call Us</div>
    <div class="fl" style="left:903px;top:138px">+1 555 014 2290</div>
    <svg class="abs" style="left:882px;top:168px" width="16" height="12" viewBox="0 0 16 12"><rect width="16" height="12" fill="#fff"/><path d="M0 0 L8 7 L16 0" fill="none" stroke="#000" stroke-width="1.5"/></svg>
    <div class="fl fb" style="left:903px;top:166px">Mail Us</div>
    <div class="fl" style="left:903px;top:194px">hello@tidypaddock.example</div>
    <svg class="abs" style="left:880px;top:223px" width="16" height="16" viewBox="0 0 16 16"><circle cx="8" cy="8" r="7" fill="none" stroke="#fff" stroke-width="1.5"/><ellipse cx="8" cy="8" rx="3" ry="7" fill="none" stroke="#fff" stroke-width="1.2"/><line x1="1" y1="8" x2="15" y2="8" stroke="#fff" stroke-width="1.2"/></svg>
    <div class="fl fb" style="left:903px;top:223px">Website</div>
    <div class="fl" style="left:903px;top:251px">www.tidypaddock.example</div>
    <svg class="abs" style="left:884px;top:279px" width="12" height="16" viewBox="0 0 12 16"><path d="M6 16 C2 10 0 8 0 6 A6 6 0 0 1 12 6 C12 8 10 10 6 16 Z" fill="#fff"/><circle cx="6" cy="6" r="2" fill="#000"/></svg>
    <div class="fl fb" style="left:903px;top:279px">Location</div>
    <div class="fl" style="left:903px;top:307px">Lorem Ipsum</div>
    <div class="fl" style="left:903px;top:335px">Lorem Ipsum</div>

    <div class="abs" style="left:110px;top:376px;width:976px;height:2px;background:#fff"></div>
    <div class="fl" style="left:0;width:1200px;text-align:center;top:397px;font-size:13.5px">© 2024 &nbsp;Tidy paddock Services I All Rights Reserved</div>
  </div>
</footer>

</body>
</html>
```